Website Redesign for MarrowArc.co.za – Bold, Modern & Professional Tattoo Supply Store (B2B ...

We’re looking for a skilled and creative web designer to redesign MarrowArc.co.za, a leading tattoo equipment and supplies store based in South Africa. The business serves both B2B (tattoo studios, artists, wholesalers) and B2C (individual customers) markets.

The current website is outdated and lacks the modern, edgy look that reflects the tattoo industry. We want a fresh, bold, and professional design that appeals to both professional artists and retail customers — combining trust, style, and functionality.

About the Business:
Marrow Arc supplies a wide range of tattoo-related products, including machines, needles, inks, hygiene supplies, and accessories. The company is well-established in the South African market and serves both individual tattoo artists and studios, as well as end customers looking for quality equipment.

The website must reflect the creative, bold, and artistic nature of the tattoo industry, while still being easy to navigate, fast, and conversion-focused.

What We’re Looking For:
A bold, modern design with a clear structure
Strong visual identity that reflects the tattoo culture — edgy, artistic, but still clean and professional
A layout that works for both B2B and B2C audiences
Clear product presentation and strong CTAs (Buy Now, Request Quote, Contact, etc.)
Fully responsive design (desktop + mobile)
Easy-to-navigate product categories and filters
Space for featured products, promotions, and artist-focused content
Integration of trust elements (payment icons, reviews, certifications, etc.)

Pages We Need Designed:
Homepage
Product detail page

Inspiration / Style Direction:
We’re looking for something with a strong personality, inspired by tattoo culture, but still clean and user-friendly. Think:

Dark theme with bold highlights (but open to light themes if well executed)
High-quality visuals and product imagery

Examples for inspiration:
GrimQuill.co.uk
Wexley RPN
Corvane Needle Supply
Brisk Tallow

Deliverables:
Full desktop and mobile designs (Figma, XD, or PSD)
All design source files
Fonts, icons, and assets used
Clearly labeled layers and organized files
Ready for development handoff

Target Market(s)

MarrowArc.co.za targets both B2B and B2C customers in South Africa: B2B: Professional tattoo artists, studios, and wholesalers looking for high-quality, reliable equipment and bulk pricing. B2C: Individual customers, hobbyists, and beginners seeking safe, affordable tattoo supplies with guidance and support. The site should appeal to both experienced professionals and newcomers, combining a bold, authentic tattoo vibe with a clean, user-friendly shopping experience.

Industry/Entity Type

Tattoo Equipment & Supplies – E-commerce (B2B & B2C)

Number of Pages Required

2 page

Requirements
Must have
• Responsive design, bold tattoo-inspired visual style, clear navigation for B2B & B2C, strong product presentation, clear call-to-actions, trust elements (reviews, badges, payment icons), category filters & search, dedicated B2B/wholesale info page, speed-optimized layout, easy access to contact & support.
Should not have
• Overly complex animations, cluttered layout, generic stock images, too many fonts or colors, hidden navigation, auto-play videos or sounds, outdated visual styles, low-quality product images, confusing checkout process, unnecessary pop-ups.

```html
<!DOCTYPE html>
<html lang="en">
<head>
<meta charset="utf-8">
<title>Marrow Arc – Professional Tattoo Equipment & Supplies</title>
<link href="https://fonts.googleapis.com/css2?family=Cinzel:wght@500;600;700&family=Poppins:wght@300;400;500;600&display=swap" rel="stylesheet">
<style>
:root{
  --red:#d9273a;
  --red-soft:#e4505f;
  --black:#0d0d0d;
  --ink:#151515;
  --panel:#1f1f1f;
  --about:#2b2b2b;
  --white:#ffffff;
  --tile:#fafafa;
  --star:#f5b50a;
}
*{box-sizing:border-box;margin:0;padding:0}
html,body{width:1200px;height:3979px;overflow:hidden}
body{position:relative;background:var(--black);color:var(--white);font-family:'Poppins',sans-serif}
.abs{position:absolute}
.serif{font-family:'Cinzel',serif;font-weight:700}
svg{display:block}

/* header */
.topbar{left:0;top:0;width:1200px;height:92px;background:var(--black)}
.promo{left:401px;top:0;width:799px;height:31px;background:var(--red);clip-path:polygon(12px 0,100% 0,100% 100%,0 100%)}
.promo-link{font-size:12px;top:8px;display:flex;align-items:center;gap:6px}
.promo-off{left:427px;top:6px;font-size:14px;font-weight:600}
.brand{font-size:30px;font-weight:600;letter-spacing:1px}
.search{left:570px;top:46px;width:325px;height:34px;border:1px solid #3a3a3a;border-radius:3px;background:#141414;font-size:12px;color:#777;padding:8px 12px}
.cartinfo{left:916px;top:55px;font-size:12px}
.cartbtn{left:1029px;top:50px;width:28px;height:28px;border-radius:50%;background:#333;display:flex;align-items:center;justify-content:center}
.nav{left:0;top:92px;width:1200px;height:42px;background:#1a1a1a}
.nav span{position:absolute;top:13px;font-size:12px;color:#ddd}
.nav .on{color:#fff;font-weight:500}

/* hero */
.hero{left:0;top:134px;width:1200px;height:564px;
  background:
   radial-gradient(ellipse 180px 140px at 930px 250px,rgba(150,120,95,.55),transparent 70%),
   radial-gradient(ellipse 260px 170px at 800px 470px,rgba(170,130,105,.6),transparent 70%),
   radial-gradient(ellipse 200px 200px at 700px 300px,rgba(10,10,10,.7),transparent 70%),
   linear-gradient(90deg,#161616 0%,#1f1f1f 38%,#3a322d 58%,#4f4036 75%,#2c2826 100%)}
.hero-title{left:141px;top:210px;font-size:46px;line-height:65px;font-variant:small-caps;font-weight:600}
.hero-copy{left:141px;top:414px;font-size:16px;line-height:30px;color:#e6e6e6}
.btn{display:flex;align-items:center;justify-content:center;font-size:14px;border-radius:2px}
.btn-red{background:var(--red)}
.btn-line{border:1px solid #ddd}
.thumb{left:993px;width:170px;border-radius:4px}

/* features */
.features{left:0;top:698px;width:1200px;height:120px;background:var(--red)}
.feat{top:34px;display:flex;gap:16px}
.feat h4{font-size:19px;font-weight:500}
.feat p{font-size:15px;color:#ffe1e4;font-weight:300;margin-top:2px}

/* categories */
.cats{left:0;top:818px;width:1200px;height:776px;background:var(--panel)}
.section-title{width:1200px;text-align:center;font-size:27px;font-variant:small-caps}
.cat-img{width:211px;height:211px;border-radius:4px;background-color:var(--tile)}
.cat-label{width:211px;text-align:center;font-size:17px}

/* featured */
.tabs{left:481px;top:1777px;width:239px;height:37px;background:#fff;border-radius:2px;display:flex;font-size:13px;align-items:center}
.prod{top:1843px;width:282px;height:444px;border:1px solid #333;border-radius:3px;background:#111}
.prod-img{left:0;top:0;width:280px;height:196px;background-color:#fff}
.prod-name{left:16px;top:220px;font-size:16px;line-height:28px}
.stars{left:16px;top:292px;display:flex;gap:3px;align-items:center;font-size:13px}
.price{left:16px;top:329px;font-size:21px}
.price s{font-size:13px;color:#999;margin-left:8px}
.addcart{left:16px;top:383px;width:248px;height:42px;background:#202020;font-size:13px;gap:8px}
.addcart.hot{background:var(--red)}
.pager{display:flex;align-items:center;gap:10px}
.dot{width:5px;height:5px;border-radius:50%;background:#777}
.dot.on{width:7px;height:7px;background:var(--red)}

/* about */
.about{left:0;top:2400px;width:1200px;height:435px;background:var(--about)}
.about-img{left:141px;top:2481px;width:423px;height:270px;border-radius:3px;
  background:radial-gradient(ellipse 190px 115px at 50% 56%,#151515 0%,#1e1e1e 65%,rgba(255,255,255,0) 100%),#f6f6f6}
.check{display:flex;align-items:center;gap:10px;font-size:12px;color:#e8e8e8}

/* reviews */
.review{top:2992px;width:340px;height:204px;background:#1c1c1c;border-left:2px solid #2c2c2c;border-right:2px solid #2c2c2c;padding:36px 28px}
.review p{font-size:13px;line-height:26px;color:#e6e6e6;margin-top:18px;white-space:nowrap}
.review b{display:block;font-size:14px;font-weight:500;margin-top:16px}

/* cta */
.cta{left:0;top:3330px;width:1200px;height:283px;background:var(--red);overflow:hidden}
.cta-title{left:141px;top:3395px;font-size:40px;line-height:57px;font-variant:small-caps}
.input{left:639px;top:3446px;width:294px;height:50px;background:var(--red-soft);border-radius:3px 0 0 3px;font-size:13px;color:#ffe6e8;padding:15px 20px}
.submit{left:933px;top:3446px;width:125px;height:50px;background:#fff;color:#111;font-size:15px;font-weight:500;border-radius:0 3px 3px 0}

/* footer */
.footer{left:0;top:3613px;width:1200px;height:310px;background:var(--ink)}
.foot-h{font-size:15px;font-weight:500}
.foot-link{font-size:12px;color:#cfcfcf}
.social{width:26px;height:26px;border-radius:50%;border:1px solid #555}
.ci{width:32px;height:32px;border-radius:50%;background:#fff;display:flex;align-items:center;justify-content:center}
.copy{left:0;top:3923px;width:1200px;height:56px;background:#1e1e1e;text-align:center;font-size:12px;color:#bbb;padding-top:27px}
</style>
</head>
<body>

<!-- header -->
<div class="abs topbar"></div>
<div class="abs promo"></div>
<div class="abs promo-off">Get 50% Off</div>
<div class="abs promo-link" style="left:610px">
  <svg width="14" height="14" viewBox="0 0 24 24" fill="none" stroke="#fff" stroke-width="2"><circle cx="12" cy="8" r="4"/><path d="M4 21c1-4 4-6 8-6s7 2 8 6"/></svg>Account</div>
<div class="abs promo-link" style="left:718px">
  <svg width="15" height="14" viewBox="0 0 24 22" fill="none" stroke="#fff" stroke-width="2"><path d="M12 20S3 14 3 8a4.5 4.5 0 0 1 9-1 4.5 4.5 0 0 1 9 1c0 6-9 12-9 12z"/></svg>Wish list (1)</div>
<div class="abs promo-link" style="left:846px">
  <svg width="16" height="14" viewBox="0 0 26 22" fill="none" stroke="#fff" stroke-width="2"><path d="M1 2h4l3 13h13l3-9H7"/><circle cx="10" cy="19" r="1.5"/><circle cx="19" cy="19" r="1.5"/></svg>Checkout</div>
<div class="abs promo-link" style="left:965px">
  <svg width="14" height="14" viewBox="0 0 24 24" fill="none" stroke="#fff" stroke-width="2"><path d="M5 3h4l2 5-3 2a12 12 0 0 0 6 6l2-3 5 2v4a2 2 0 0 1-2 2A18 18 0 0 1 3 5a2 2 0 0 1 2-2z"/></svg>0827305519</div>

<div class="abs brand" style="left:141px;top:14px">Marrow Arc</div>

<div class="abs search">Search...
  <svg class="abs" style="right:10px;top:9px" width="14" height="14" viewBox="0 0 24 24" fill="none" stroke="#aaa" stroke-width="2"><circle cx="10" cy="10" r="7"/><path d="M15 15l6 6"/></svg></div>
<div class="abs cartinfo">10 item(s) - R150</div>
<div class="abs cartbtn"><svg width="14" height="12" viewBox="0 0 26 22" fill="none" stroke="#fff" stroke-width="2"><path d="M1 2h4l3 13h13l3-9H7"/></svg></div>

<nav class="abs nav">
  <span class="on" style="left:142px">Home</span>
  <span style="left:211px">Shop</span>
  <span style="left:273px">Tattoo Machines</span>
  <span style="left:401px">Needles &amp; Cartridges</span>
  <span style="left:557px">Hygiene &amp; Aftercare</span>
  <span style="left:707px">Accessories</span>
  <span style="left:808px">Brands</span>
  <span style="left:882px">B2B / Wholesale</span>
  <span style="left:1011px">Contact</span>
</nav>

<!-- hero -->
<div class="abs hero" role="img" aria-label="Tattoo artist in black gloves working a rotary machine on a client's arm"></div>
<h1 class="abs hero-title serif">Professional<br>Tattoo Equipment<br>&amp; Supplies</h1>
<p class="abs hero-copy">Professional machines, inks, needles &amp; hygiene products<br>trusted by top studios nationwide.</p>
<div class="abs btn btn-red" style="left:141px;top:537px;width:134px;height:47px">Shop Now</div>
<div class="abs btn btn-line" style="left:289px;top:537px;width:174px;height:47px">B2B Wholesale</div>

<div class="abs thumb" style="top:134px;height:169px;background:radial-gradient(ellipse 60px 40px at 55% 55%,#2a2a2a,#7a6a50 55%,rgba(255,255,255,0) 100%),#f3f3f3" role="img" aria-label="Cartridge grip product"></div>
<div class="abs thumb" style="top:327px;height:178px;background:radial-gradient(ellipse 65px 40px at 48% 60%,#6b4a32,#a99a8a 60%,rgba(255,255,255,0) 100%),#f1f1f1" role="img" aria-label="Sterilizer box product"></div>
<div class="abs thumb" style="top:530px;height:168px;background:radial-gradient(ellipse 30px 60px at 55% 45%,#4aa9a0,#b9d9d3 60%,rgba(255,255,255,0) 100%),linear-gradient(180deg,#f3f3f3 55%,#4a4a4a 100%)" role="img" aria-label="Needle cartridge product"></div>
<svg class="abs" style="left:1068px;top:146px" width="20" height="12" viewBox="0 0 20 12" fill="none" stroke="#666" stroke-width="2"><path d="M2 10l8-8 8 8"/></svg>
<svg class="abs" style="left:1068px;top:670px" width="20" height="12" viewBox="0 0 20 12" fill="none" stroke="#fff" stroke-width="2"><path d="M2 2l8 8 8-8"/></svg>

<!-- features -->
<div class="abs features">
  <div class="abs feat" style="left:141px">
    <svg width="40" height="40" viewBox="0 0 40 40" fill="none" stroke="#fff" stroke-width="2"><circle cx="20" cy="20" r="18"/><path d="M12 20l6 6 11-12"/></svg>
    <div><h4>Secure Payments</h4><p>Our website uses SSL</p></div></div>
  <div class="abs feat" style="left:460px">
    <svg width="40" height="40" viewBox="0 0 40 40" fill="none" stroke="#fff" stroke-width="2"><circle cx="20" cy="20" r="18"/><path d="M12 20l6 6 11-12"/></svg>
    <div><h4>Fast Shipping</h4><p>We ship the same day</p></div></div>
  <div class="abs feat" style="left:776px">
    <svg width="40" height="40" viewBox="0 0 40 40" fill="none" stroke="#fff" stroke-width="2"><circle cx="20" cy="20" r="18"/><path d="M12 20l6 6 11-12"/></svg>
    <div><h4>Extensive stock range</h4><p>All products in stock</p></div></div>
</div>

<!-- categories -->
<div class="abs cats"></div>
<h2 class="abs section-title serif" style="left:0;top:898px">Shop By Category</h2>
<div class="abs cat-img" style="left:141px;top:967px;background-image:radial-gradient(ellipse 50px 80px at 50% 52%,#8e8e8e,#c8c8c8 55%,rgba(250,250,250,0) 100%)" role="img" aria-label="Steel cartridge grips"></div>
<div class="abs cat-img" style="left:377px;top:967px;background-image:radial-gradient(ellipse 45px 85px at 52% 50%,#4fb3d8,#bfe2ef 55%,rgba(250,250,250,0) 100%)" role="img" aria-label="Blue needle cartridge"></div>
<div class="abs cat-img" style="left:612px;top:967px;background-image:radial-gradient(ellipse 70px 45px at 58% 45%,#e0352d,#f0a19a 55%,rgba(250,250,250,0) 100%)" role="img" aria-label="Red rotary tattoo machine"></div>
<div class="abs cat-img" style="left:847px;top:967px;background-image:radial-gradient(ellipse 70px 75px at 52% 52%,#111,#3a3a3a 55%,rgba(250,250,250,0) 100%)" role="img" aria-label="Black ink bottles"></div>
<div class="abs cat-label" style="left:141px;top:1197px">Cartridges</div>
<div class="abs cat-label" style="left:377px;top:1197px">Needles</div>
<div class="abs cat-label" style="left:612px;top:1197px">Tattoo Machines</div>
<div class="abs cat-label" style="left:847px;top:1197px">Inks</div>
<div class="abs cat-img" style="left:141px;top:1254px;background-image:radial-gradient(ellipse 85px 55px at 50% 55%,#6b4a32,#c9b7a6 55%,rgba(250,250,250,0) 100%)" role="img" aria-label="Sterilizer unit"></div>
<div class="abs cat-img" style="left:377px;top:1254px;background-image:radial-gradient(ellipse 70px 65px at 52% 55%,#6fb79d,#b9dccf 55%,rgba(250,250,250,0) 100%)" role="img" aria-label="Aftercare tubes"></div>
<div class="abs cat-img" style="left:612px;top:1254px;background-image:radial-gradient(ellipse 85px 60px at 50% 52%,#a8a8a8,#dedede 55%,rgba(250,250,250,0) 100%)" role="img" aria-label="Rinse cup tray"></div>
<div class="abs cat-img" style="left:847px;top:1254px;background-image:radial-gradient(ellipse 45px 85px at 50% 50%,#1a1a1a,#8a8a8a 45%,rgba(250,250,250,0) 100%)" role="img" aria-label="Adjustable arm rest stand"></div>
<div class="abs cat-label" style="left:141px;top:1484px">Power Supplies</div>
<div class="abs cat-label" style="left:377px;top:1484px">Hygiene &amp; Aftercare</div>
<div class="abs cat-label" style="left:612px;top:1484px">Accessories</div>
<div class="abs cat-label" style="left:847px;top:1484px">Studio Equipment</div>

<!-- featured -->
<h2 class="abs section-title" style="left:0;top:1676px;font-family:'Cinzel',serif;font-weight:700;font-variant:normal">FEATURED PRODUCTS / BESTSELLERS</h2>
<p class="abs" style="left:0;top:1728px;width:1200px;text-align:center;font-size:13px;color:#ddd">At MarrowArc we like to ensure that the tattoo industry standards are maintained.</p>
<div class="abs tabs">
  <div style="background:var(--red);height:33px;margin-left:2px;padding:0 10px;display:flex;align-items:center;font-size:12px">Featured Products</div>
  <div style="color:var(--red);padding-left:12px;font-size:13px">Best Sellers</div>
</div>

<svg width="0" height="0" style="position:absolute"><defs>
  <path id="st" d="M7 0l2 5h5l-4 3 2 5-5-3-5 3 2-5-4-3h5z"/>
  <path id="q" d="M0 20V10C0 4 3 1 9 0v4c-3 1-4 3-4 6h5v10zM15 20V10c0-6 3-9 9-10v4c-3 1-4 3-4 6h5v10z"/>
</defs></svg>

<div class="abs prod" style="left:141px">
  <div class="abs prod-img" style="background-image:radial-gradient(ellipse 28px 78px at 50% 55%,#3c3a9a,#8f8dd0 55%,rgba(255,255,255,0) 100%)" role="img" aria-label="Deep purple ink bottle"></div>
  <div class="abs prod-name">Halden Tattoo Ink Deep<br>Purple 1oz - Halden Tattoo Ink</div>
  <div class="abs stars"><svg width="92" height="14" viewBox="0 0 92 14" fill="#f5b50a"><use href="#st"/><use href="#st" x="19"/><use href="#st" x="38"/><use href="#st" x="57"/><use href="#st" x="76"/></svg><span style="margin-left:6px">(4.8)</span></div>
  <div class="abs price">$ 2,500<s>$ 2,560</s></div>
  <div class="abs btn addcart">Add to cart <svg width="16" height="14" viewBox="0 0 26 22" fill="none" stroke="#fff" stroke-width="2"><path d="M1 2h4l3 13h13l3-9H7"/><circle cx="10" cy="19" r="1.5"/><circle cx="19" cy="19" r="1.5"/></svg></div>
</div>
<div class="abs prod" style="left:459px">
  <div class="abs prod-img" style="background-image:radial-gradient(ellipse 105px 55px at 50% 52%,#151515,#4a4a4a 55%,rgba(255,255,255,0) 100%)" role="img" aria-label="Pile of black ink caps"></div>
  <div class="abs prod-name">Halden Tattoo Ink Deep<br>Purple 1oz - Halden Tattoo Ink</div>
  <div class="abs stars"><svg width="92" height="14" viewBox="0 0 92 14" fill="#f5b50a"><use href="#st"/><use href="#st" x="19"/><use href="#st" x="38"/><use href="#st" x="57"/><use href="#st" x="76"/></svg><span style="margin-left:6px">(4.8)</span></div>
  <div class="abs price">$ 1,550<s>$ 2,560</s></div>
  <div class="abs btn addcart hot">Add to cart <svg width="16" height="14" viewBox="0 0 26 22" fill="none" stroke="#fff" stroke-width="2"><path d="M1 2h4l3 13h13l3-9H7"/><circle cx="10" cy="19" r="1.5"/><circle cx="19" cy="19" r="1.5"/></svg></div>
</div>
<div class="abs prod" style="left:777px">
  <div class="abs prod-img" style="background-image:radial-gradient(ellipse 28px 78px at 50% 55%,#0e1a3a,#5a6a90 55%,rgba(255,255,255,0) 100%)" role="img" aria-label="Dark blue ink bottle"></div>
  <div class="abs prod-name">Halden Tattoo Ink Deep<br>Purple 1oz - Halden Tattoo Ink</div>
  <div class="abs stars"><svg width="92" height="14" viewBox="0 0 92 14" fill="#f5b50a"><use href="#st"/><use href="#st" x="19"/><use href="#st" x="38"/><use href="#st" x="57"/><use href="#st" x="76"/></svg><span style="margin-left:6px">(4.8)</span></div>
  <div class="abs price">$ 2,500<s>$ 2,560</s></div>
  <div class="abs btn addcart">Add to cart <svg width="16" height="14" viewBox="0 0 26 22" fill="none" stroke="#fff" stroke-width="2"><path d="M1 2h4l3 13h13l3-9H7"/><circle cx="10" cy="19" r="1.5"/><circle cx="19" cy="19" r="1.5"/></svg></div>
</div>
<div class="abs pager" style="left:512px;top:2305px">
  <svg width="20" height="12" viewBox="0 0 20 12" fill="none" stroke="#fff" stroke-width="1.6"><path d="M19 6H2M7 1L2 6l5 5"/></svg>
  <span style="width:30px"></span><i class="dot"></i><i class="dot"></i><i class="dot on"></i><i class="dot"></i><i class="dot"></i><span style="width:30px"></span>
  <svg width="20" height="12" viewBox="0 0 20 12" fill="none" stroke="#fff" stroke-width="1.6"><path d="M1 6h17M13 1l5 5-5 5"/></svg>
</div>

<!-- about -->
<div class="abs about"></div>
<div class="abs about-img" role="img" aria-label="Four grey wash ink bottles in a row"></div>
<h2 class="abs serif" style="left:599px;top:2480px;font-size:29px;font-variant:small-caps">About Us</h2>
<h3 class="abs" style="left:599px;top:2531px;font-size:21px;font-weight:400">South Africa’s Trusted Tattoo Supply Partner</h3>
<p class="abs" style="left:599px;top:2574px;width:470px;font-size:13px;line-height:24px;color:#ddd">There are many variations of passages of Lorem Ipsum available, but the majority have suffered alteration in some form, by injected humour, or words which don't look even slightly believable.</p>
<div class="abs check" style="left:599px;top:2664px"><svg width="16" height="16" viewBox="0 0 20 20" fill="none" stroke="#fff" stroke-width="1.5"><circle cx="10" cy="10" r="8.5"/><path d="M6 10l3 3 5-6"/></svg>100% genuine branded products</div>
<div class="abs check" style="left:599px;top:2698px"><svg width="16" height="16" viewBox="0 0 20 20" fill="none" stroke="#fff" stroke-width="1.5"><circle cx="10" cy="10" r="8.5"/><path d="M6 10l3 3 5-6"/></svg>Dedicated service &amp; expert guidance</div>
<div class="abs check" style="left:599px;top:2732px"><svg width="16" height="16" viewBox="0 0 20 20" fill="none" stroke="#fff" stroke-width="1.5"><circle cx="10" cy="10" r="8.5"/><path d="M6 10l3 3 5-6"/></svg>Fast shipping across South Africa</div>

<!-- reviews -->
<h2 class="abs section-title serif" style="left:0;top:2916px">Customer Reviews</h2>
<div class="abs review" style="left:-124px"><svg width="26" height="20" viewBox="0 0 26 20" fill="#d9273a"><use href="#q"/></svg><p>Lorem Ipsum has been the industry's fact<br>that standard dummy text ever since the.</p><b>~ J.R., Portland</b></div>
<div class="abs review" style="left:247px"><svg width="26" height="20" viewBox="0 0 26 20" fill="#d9273a"><use href="#q"/></svg><p>Lorem Ipsum has been the industry's fact<br>that standard dummy text ever since the.</p><b>~ A.B., Chicago</b></div>
<div class="abs review" style="left:618px"><svg width="26" height="20" viewBox="0 0 26 20" fill="#d9273a"><use href="#q"/></svg><p>Lorem Ipsum has been the industry's fact<br>that standard dummy text ever since the.</p><b>~ T.T., Denver</b></div>
<div class="abs review" style="left:988px"><svg width="26" height="20" viewBox="0 0 26 20" fill="#d9273a"><use href="#q"/></svg><p>Lorem Ipsum has been the industry's fact<br>that standard dummy text ever since the.</p><b>~ C.D., Austin</b></div>
<div class="abs pager" style="left:512px;top:3236px">
  <svg width="20" height="12" viewBox="0 0 20 12" fill="none" stroke="#fff" stroke-width="1.6"><path d="M19 6H2M7 1L2 6l5 5"/></svg>
  <span style="width:30px"></span><i class="dot"></i><i class="dot"></i><i class="dot on"></i><i class="dot"></i><i class="dot"></i><span style="width:30px"></span>
  <svg width="20" height="12" viewBox="0 0 20 12" fill="none" stroke="#fff" stroke-width="1.6"><path d="M1 6h17M13 1l5 5-5 5"/></svg>
</div>

<!-- cta -->
<div class="abs cta">
  <svg class="abs" style="left:0;top:0" width="1200" height="283" viewBox="0 0 1200 283"><path d="M0 0h60L0 60z" fill="#e03446"/><path d="M1090 0h110v283h-200z" fill="#dd3143"/></svg>
</div>
<h2 class="abs cta-title serif">Ready To Upgrade<br>Your Studio?</h2>
<p class="abs" style="left:141px;top:3520px;font-size:16px">Get exclusive wholesale pricing support for your business</p>
<div class="abs input">Enter Email</div>
<div class="abs btn submit">Submit</div>

<!-- footer -->
<div class="abs footer"></div>
<div class="abs brand" style="left:141px;top:3716px;font-size:36px">Marrow Arc</div>
<div class="abs" style="left:139px;top:3835px;font-size:12px">Follow Us:</div>
<div class="abs social" style="left:215px;top:3829px"></div>
<div class="abs social" style="left:252px;top:3829px;background:var(--red);border-color:var(--red)"></div>
<div class="abs social" style="left:289px;top:3829px"></div>
<div class="abs" style="left:411px;top:3690px;width:1px;height:190px;background:#333"></div>
<div class="abs" style="left:798px;top:3690px;width:1px;height:190px;background:#333"></div>

<div class="abs foot-h" style="left:472px;top:3694px">Quick Links</div>
<div class="abs foot-link" style="left:472px;top:3742px">Home</div>
<div class="abs foot-link" style="left:472px;top:3770px">Shop</div>
<div class="abs foot-link" style="left:472px;top:3799px">Tattoo Machines</div>
<div class="abs foot-link" style="left:472px;top:3829px">Needles &amp; Cartridges</div>
<div class="abs foot-link" style="left:472px;top:3858px">Hygiene &amp; Aftercare</div>
<div class="abs foot-link" style="left:638px;top:3742px">Accessories</div>
<div class="abs foot-link" style="left:638px;top:3770px">Brands</div>
<div class="abs foot-link" style="left:638px;top:3799px">B2B / Wholesale</div>
<div class="abs foot-link" style="left:638px;top:3829px">Contact</div>

<div class="abs foot-h" style="left:860px;top:3694px">Contact Us</div>
<div class="abs ci" style="left:860px;top:3745px"><svg width="12" height="14" viewBox="0 0 20 24" fill="none" stroke="#111" stroke-width="2.4"><path d="M10 22s8-7 8-13a8 8 0 0 0-16 0c0 6 8 13 8 13z"/><circle cx="10" cy="9" r="3"/></svg></div>
<div class="abs foot-link" style="left:905px;top:3742px;line-height:21px;color:#fff">MarrowArc Pty Ltd Po Box<br>40218 Kelvale 0093</div>
<div class="abs ci" style="left:860px;top:3804px;background:var(--red)"><svg width="14" height="14" viewBox="0 0 24 24" fill="#fff"><path d="M5 3h4l2 5-3 2a12 12 0 0 0 6 6l2-3 5 2v4a2 2 0 0 1-2 2A18 18 0 0 1 3 5a2 2 0 0 1 2-2z"/></svg></div>
<div class="abs foot-link" style="left:905px;top:3812px;color:#fff">Phone: 0827305519</div>
<div class="abs ci" style="left:860px;top:3855px"><svg width="14" height="11" viewBox="0 0 24 18" fill="none" stroke="#111" stroke-width="2.4"><rect x="1" y="1" width="22" height="16" rx="2"/><path d="M1 2l11 8 11-8"/></svg></div>
<div class="abs foot-link" style="left:905px;top:3862px;color:#fff">info@marrowarc.co.za</div>

<div class="abs copy">© 2025 Marrow Arc. All rights reserved.</div>

</body>
</html>
```